Brightwater Care Partners, LLC Business Card update!

would like a classier business card. Our cards currently just have our logo and contact information. Need better use of color and creativity
Logo attached.

Target Market(s)

Potential clients, contacts, existing clients. We are a consulting company

Industry/Entity Type

Business

Contact Information for Business Card

We like our colors but just have a boring card with our logo and a white background. I want something that stands out.

Colors
ec1f27
757575

Requirements
Must have
• Color to stay consistent. Logo provided
Nice to have
• Just better use of color/ design

```html
<!DOCTYPE html>
<html lang="en">
<head>
<meta charset="UTF-8">
<title>Brightwater Care Partners — Business Card</title>
<link rel="stylesheet" href="https://fonts.googleapis.com/css2?family=Roboto+Slab:wght@400;700&display=swap">
<style>
  :root {
    --brand-red: #ec1f27;
    --brand-grey: #757575;
    --ink: #2b2b2b;
    --stage: #e6e6e6;
    --metal-light: #f4f5f6;
    --metal-mid: #dcdfe2;
    --metal-dark: #c7cbcf;
    --divider: #b9bcbf;
  }
  * { box-sizing: border-box; margin: 0; padding: 0; }
  html, body {
    width: 1200px;
    height: 882px;
    overflow: hidden;
    background: var(--stage);
  }
  .business-card {
    position: absolute;
    left: 150px;
    top: 181px;
    width: 900px;
    height: 520px;
    border-radius: 36px;
    background: linear-gradient(160deg, var(--metal-light) 0%, var(--metal-mid) 45%, var(--metal-light) 70%, var(--metal-dark) 100%);
    box-shadow: 0 10px 30px rgba(0, 0, 0, 0.18);
    font-family: "Roboto Slab", serif;
    color: var(--ink);
  }
  .brand-lockup {
    position: absolute;
    left: 120px;
    top: 92px;
    display: flex;
    align-items: center;
    gap: 24px;
  }
  .brand-dot {
    width: 58px;
    height: 58px;
    border-radius: 50%;
    background: var(--brand-red);
    flex: none;
  }
  .brand-name {
    font-size: 50px;
    font-weight: 400;
    color: var(--brand-grey);
    line-height: 1;
    white-space: nowrap;
  }
  .contact-block {
    position: absolute;
    left: 0;
    right: 0;
    top: 300px;
    display: flex;
    justify-content: center;
  }
  .identity {
    width: 330px;
    text-align: right;
    padding-right: 26px;
  }
  .person-name {
    font-size: 31px;
    font-weight: 700;
    color: var(--brand-red);
    line-height: 1.1;
  }
  .person-title {
    font-size: 21px;
    font-weight: 700;
    margin-top: 4px;
  }
  .address {
    font-size: 21px;
    line-height: 1.3;
    margin-top: 28px;
  }
  .divider {
    width: 2px;
    background: var(--divider);
    align-self: stretch;
  }
  .channels {
    list-style: none;
    padding-left: 26px;
    width: 380px;
  }
  .channel {
    display: flex;
    align-items: center;
    gap: 14px;
    font-size: 22px;
    height: 42px;
  }
  .channel-icon {
    width: 22px;
    height: 22px;
    flex: none;
  }
</style>
</head>
<body>
  <main class="business-card">
    <div class="brand-lockup">
      <span class="brand-dot"></span>
      <span class="brand-name">Brightwater Care Partners</span>
    </div>

    <section class="contact-block">
      <div class="identity">
        <p class="person-name">Your Name</p>
        <p class="person-title">Title</p>
        <p class="address">Street Name, City Name<br>State Zipcode</p>
      </div>
      <div class="divider"></div>
      <ul class="channels">
        <li class="channel">
          <svg class="channel-icon" viewBox="0 0 22 22" aria-hidden="true">
            <circle cx="11" cy="11" r="11" fill="var(--brand-red)"/>
            <path d="M7.5 5.5 L9.5 5.5 L10.3 8.3 L9 9.4 C9.6 10.9 10.9 12.3 12.5 13 L13.6 11.7 L16.4 12.5 L16.4 14.5 C16.4 15.5 15.5 16.4 14.4 16.2 C10 15.6 6.4 12 5.8 7.6 C5.6 6.5 6.5 5.5 7.5 5.5 Z" fill="#fff"/>
          </svg>
          <span>123-456-7890</span>
        </li>
        <li class="channel">
          <svg class="channel-icon" viewBox="0 0 22 22" aria-hidden="true">
            <rect x="2" y="5" width="18" height="12" rx="1.5" fill="var(--brand-red)"/>
            <path d="M3 6 L11 12 L19 6" fill="none" stroke="#fff" stroke-width="1.6"/>
          </svg>
          <span>brightwatercp@mail.com</span>
        </li>
        <li class="channel">
          <svg class="channel-icon" viewBox="0 0 22 22" aria-hidden="true">
            <circle cx="11" cy="11" r="11" fill="var(--brand-red)"/>
            <circle cx="11" cy="11" r="6" fill="none" stroke="#fff" stroke-width="1.4"/>
            <ellipse cx="11" cy="11" rx="2.6" ry="6" fill="none" stroke="#fff" stroke-width="1.2"/>
            <line x1="5" y1="11" x2="17" y2="11" stroke="#fff" stroke-width="1.2"/>
          </svg>
          <span>brightwatercp.com</span>
        </li>
        <li class="channel">
          <svg class="channel-icon" viewBox="0 0 22 22" aria-hidden="true">
            <circle cx="11" cy="11" r="11" fill="var(--brand-red)"/>
            <circle cx="11" cy="11" r="5.5" fill="none" stroke="#fff" stroke-width="1.6"/>
            <circle cx="11" cy="11" r="2" fill="#fff"/>
          </svg>
          <span>www.brightwatercp.com</span>
        </li>
      </ul>
    </section>
  </main>
</body>
</html>
```